Veldmark Supplies Business Card

Professional business card that stand out to our potential customers. Front and back with clean modern design

Industry/Entity Type

Oil and gas

Contact Information for Business Card

Name, address, website , office phone and cell number

Requirements
Must have
• Editable files for each employee

```html
<!DOCTYPE html>
<html lang="en">
<head>
<meta charset="utf-8">
<title>Veldmark Supplies Business Card</title>
<link rel="stylesheet" href="https://fonts.googleapis.com/css2?family=Arimo:wght@400;700&display=swap">
<style>
  :root {
    --stage: #3b3b3d;
    --card-white: #ffffff;
    --brand-blue: #06afd2;
    --brand-red: #f20a12;
    --ink-white: #ffffff;
  }
  * { box-sizing: border-box; margin: 0; padding: 0; }
  html, body { width: 1200px; height: 689px; overflow: hidden; }
  body {
    background: var(--stage);
    font-family: "Arimo", Arial, sans-serif;
    position: relative;
  }
  .card {
    position: absolute;
    top: 195px;
    width: 520px;
    height: 297px;
    border-radius: 18px;
    overflow: hidden;
  }
  .card--front { left: 50px; background: var(--card-white); }
  .card--back { left: 630px; background: var(--brand-blue); }

  .brand {
    display: flex;
    align-items: center;
    gap: 10px;
    font-weight: 700;
    text-transform: uppercase;
    letter-spacing: 0.04em;
  }
  .brand__mark { display: block; background: var(--brand-red); }

  .card--front .brand {
    position: absolute;
    left: 0; right: 0; top: 0; bottom: 0;
    justify-content: center;
    color: var(--brand-red);
    font-size: 30px;
  }
  .card--front .brand__mark { width: 30px; height: 30px; }

  .back__panel {
    position: absolute;
    right: 0; top: 0;
    width: 220px; height: 297px;
  }

  .back__info {
    position: absolute;
    left: 36px; top: 46px;
    color: var(--ink-white);
  }
  .card--back .brand { color: var(--ink-white); font-size: 19px; }
  .card--back .brand__mark { width: 18px; height: 18px; background: var(--ink-white); }

  .person { margin-top: 26px; }
  .person__name { color: var(--brand-red); font-size: 22px; font-weight: 700; }
  .person__role { font-size: 13px; margin-top: 2px; }

  .address { margin-top: 18px; font-size: 13px; line-height: 1.35; font-style: normal; }

  .contacts { list-style: none; margin-top: 14px; font-size: 13px; line-height: 1.45; }
  .contacts li { display: flex; align-items: center; gap: 8px; }
  .contacts svg { width: 11px; height: 11px; fill: var(--brand-red); flex: none; }
</style>
</head>
<body>

<section class="card card--front" aria-label="Card front">
  <div class="brand">
    <span class="brand__mark"></span>
    <span class="brand__name">Veldmark Supplies</span>
  </div>
</section>

<section class="card card--back" aria-label="Card back">
  <svg class="back__panel" viewBox="0 0 220 297" aria-hidden="true">
    <polygon points="60,0 220,0 220,297 80,297 0,148" fill="#ffffff"/>
  </svg>

  <div class="back__info">
    <div class="brand">
      <span class="brand__mark"></span>
      <span class="brand__name">Veldmark Supplies</span>
    </div>

    <div class="person">
      <p class="person__name">Dana Reyes</p>
      <p class="person__role">President</p>
    </div>

    <address class="address">
      4210 Larkspur Road<br>
      Calgary, Canada 51820
    </address>

    <ul class="contacts">
      <li>
        <svg viewBox="0 0 12 12"><path d="M2 0.5l2.2 0 1 2.8-1.4 1a6 6 0 0 0 3.9 3.9l1-1.4 2.8 1 0 2.2c0 0.6-0.5 1-1 1A10.5 10.5 0 0 1 1 1.5c0-0.5 0.4-1 1-1z"/></svg>
        555-210-4471
      </li>
      <li>
        <svg viewBox="0 0 12 12"><path d="M3 0h6a1 1 0 0 1 1 1v10a1 1 0 0 1-1 1H3a1 1 0 0 1-1-1V1a1 1 0 0 1 1-1zm0.5 1.5v8h5v-8z"/></svg>
        555-210-8832
      </li>
      <li>
        <svg viewBox="0 0 12 12"><path d="M0 2h12v8H0zm1 1v0.4l5 3.3 5-3.3V3z"/></svg>
        info@veldmarksupplies.com
      </li>
      <li>
        <svg viewBox="0 0 12 12"><circle cx="6" cy="6" r="6"/></svg>
        www.veldmarksupplies.com
      </li>
    </ul>
  </div>
</section>

</body>
</html>
```